Update informational website

I need a new modern site design for my website.

Here is the site: http://q.zq/kpTr

Here is a theme I liked: http://q.zq/kpTm

I am looking for something with clean lines and an exciting designs and graphics, please use images from brindlecove.com and track the images used so I can buy them if I like the design.

I just need the homepage and one interior page designed.

Colors
Bright Green #6ed30d
Dark Text #222
Lighter Text #444

Number of Pages Required

2 page

Font styles to use
Sans Serif

Requirements
Must have
• Clean, good spacing, responsive design, high resolution design

```html
<!DOCTYPE html>
<html lang="en">
<head>
<meta charset="utf-8">
<title>Mesa Glass Tint – Home</title>
<link href="https://fonts.googleapis.com/css2?family=Roboto:wght@400;500;700;900&family=Open+Sans:wght@400;600;700&display=swap" rel="stylesheet">
<style>
:root{
  --green:#6ed30d;
  --dark:#222;
  --text:#444;
  --muted:#777;
  --line:#cfcfcf;
  --white:#fff;
  --footer:#1b1b1b;
  --heading:'Roboto',Arial,sans-serif;
  --body:'Open Sans',Arial,sans-serif;
}
*{box-sizing:border-box;margin:0;padding:0}
html,body{width:1200px;height:3495px;overflow:hidden}
body{position:relative;font-family:var(--body);color:var(--text);background:var(--white)}
.abs{position:absolute}

/* hero */
.hero{position:absolute;left:0;top:0;width:1200px;height:541px;overflow:hidden}
.hero-photo{position:absolute;inset:0;background:
  radial-gradient(ellipse 260px 150px at 800px 310px,rgba(205,210,215,.55),rgba(205,210,215,0) 70%),
  radial-gradient(ellipse 520px 90px at 430px 300px,rgba(255,196,110,.9),rgba(255,160,80,0) 70%),
  radial-gradient(ellipse 200px 260px at 560px 560px,rgba(120,110,105,.6),rgba(0,0,0,0) 70%),
  linear-gradient(180deg,#2f2a2d 0%,#5a3a2e 20%,#a85b2e 38%,#d98a45 47%,#7d4a33 56%,#3f3534 72%,#1c1b1e 100%)}
.brand{position:absolute;left:98px;top:42px;display:flex;align-items:center;gap:12px;font-family:var(--heading);font-weight:900;font-size:30px;color:var(--green)}
.brand-dot{width:34px;height:34px;border-radius:50%;background:var(--green)}
.call{position:absolute;right:100px;top:16px;display:flex;align-items:center;gap:10px;font-family:var(--heading);font-weight:700;font-size:16px;color:var(--white)}
.call-icon{width:30px;height:30px;border-radius:50%;border:2px solid var(--green);display:flex;align-items:center;justify-content:center}
.call b{color:var(--green);font-size:22px}
.nav{position:absolute;right:100px;top:68px;display:flex;gap:32px;font-family:var(--heading);font-weight:700;font-size:15px;color:var(--white);align-items:center}
.nav .active{color:var(--green)}
.hero-title{position:absolute;left:98px;top:210px;font-family:var(--heading);font-weight:900;font-size:46px;color:var(--white)}
.hero-lead{position:absolute;left:98px;top:274px;width:520px;font-size:22px;line-height:30px;color:var(--white)}
.btn-outline{position:absolute;left:98px;top:366px;width:168px;height:50px;border:2px solid var(--white);color:var(--white);font-family:var(--heading);font-weight:700;font-size:15px;display:flex;align-items:center;justify-content:center}
.dots{position:absolute;left:570px;top:484px;display:flex;gap:6px}
.dots span{width:12px;height:12px;border-radius:50%;border:2px solid var(--white)}
.dots span.on{background:var(--white)}

/* welcome */
.section-title{position:absolute;left:0;width:1200px;text-align:center;font-family:var(--heading);font-weight:700;font-size:30px;color:var(--dark)}
.intro{position:absolute;left:190px;top:678px;width:820px;text-align:center;font-size:14px;line-height:27px;color:var(--text)}
.card{position:absolute;text-align:center}
.card svg.frame{position:absolute;left:0;top:0}
.card h3{position:absolute;left:0;width:100%;font-family:var(--heading);font-weight:700;font-size:21px;color:var(--dark)}
.card p{position:absolute;left:26px;width:250px;font-size:12.5px;line-height:23px;color:var(--text)}
.card .btn-small{position:absolute;left:98px;width:106px;height:40px;border:2px solid #bbb;color:var(--green);font-family:var(--heading);font-weight:700;font-size:12px;display:flex;align-items:center;justify-content:center}
.card .icon{position:absolute;left:101px}

/* services */
.services{position:absolute;left:0;top:1323px;width:1200px;height:523px;overflow:hidden}
.services-photo{position:absolute;inset:0;background:
  radial-gradient(ellipse 380px 120px at 330px 260px,rgba(150,150,160,.45),rgba(0,0,0,0) 70%),
  radial-gradient(ellipse 300px 60px at 250px 420px,rgba(160,70,60,.35),rgba(0,0,0,0) 70%),
  linear-gradient(100deg,#2a2a2d 0%,#4a4a4f 35%,#3a3a3e 60%,#1f1f22 100%)}
.services h2{position:absolute;left:98px;top:78px;font-family:var(--heading);font-weight:700;font-size:28px;color:var(--white)}
.services .lead{position:absolute;left:98px;top:122px;width:500px;font-size:14px;line-height:26px;color:#ddd}
.svc{position:absolute;left:98px;display:flex;align-items:center;gap:20px;color:var(--white)}
.svc-ring{width:70px;height:70px;border-radius:50%;border:2px solid var(--white);display:flex;align-items:center;justify-content:center}
.svc h4{font-family:var(--heading);font-weight:700;font-size:18px}
.svc span{font-size:13px;color:#ddd}
.services-photo-frame{position:absolute;left:660px;top:61px;width:438px;height:403px;border:4px solid var(--white);background:
  radial-gradient(circle at 310px 120px,#fff6d6 0,#ffd98a 40px,rgba(240,170,80,.6) 110px,rgba(0,0,0,0) 200px),
  linear-gradient(90deg,rgba(0,0,0,0) 55%,rgba(90,90,100,.75) 75%,#4a4a52 100%),
  linear-gradient(180deg,#e9bd78 0%,#f3d7a0 35%,#b08a6c 62%,#4a3f3c 100%)}

/* blog */
.post{position:absolute;top:2018px;width:324px}
.post-photo{width:324px;height:182px}
.post h3{margin-top:36px;font-family:var(--heading);font-weight:700;font-size:19px;color:var(--dark)}
.post .meta{margin-top:12px;font-size:12px;color:var(--muted);display:flex;align-items:center;gap:7px}
.post p{margin-top:14px;font-size:13px;line-height:24px;color:var(--text)}
.post .more{margin-top:14px;font-family:var(--heading);font-weight:700;font-size:13px;color:var(--green)}

/* gallery */
.gallery{position:absolute;left:0;top:2424px;width:1200px;height:826px;overflow:hidden}
.gallery-photo{position:absolute;inset:0;background:
  radial-gradient(ellipse 500px 90px at 560px 700px,rgba(235,130,60,.75),rgba(0,0,0,0) 70%),
  radial-gradient(ellipse 260px 420px at 1120px 520px,rgba(40,40,46,.85),rgba(0,0,0,0) 70%),
  linear-gradient(180deg,#4f5a66 0%,#67727d 40%,#7a5a48 78%,#242326 100%)}
.gallery h2{position:absolute;left:0;top:152px;width:1200px;text-align:center;font-family:var(--heading);font-weight:700;font-size:28px;color:var(--white)}
.tile{position:absolute;width:234px;height:205px;border:4px solid #e6e6e6}
.btn-green{position:absolute;left:527px;top:691px;width:146px;height:49px;background:var(--green);color:var(--white);font-family:var(--heading);font-weight:700;font-size:15px;display:flex;align-items:center;justify-content:center}

/* footer */
.footer{position:absolute;left:0;top:3250px;width:1200px;height:245px;background:var(--footer);border-top:5px solid var(--green);color:#ddd}
.contact{position:absolute;top:40px;display:flex;align-items:center;gap:16px;font-size:13px;line-height:22px}
.ring{width:44px;height:44px;border-radius:50%;border:2px solid var(--white);display:flex;align-items:center;justify-content:center;flex:none}
.foot-links{position:absolute;left:0;top:118px;width:1200px;text-align:center;font-size:14px;color:#eee;word-spacing:4px}
.foot-rule{position:absolute;left:98px;top:163px;width:1004px;height:1px;background:#3a3a3a}
.copy{position:absolute;left:98px;top:197px;font-size:12px;color:#ccc}
.social{position:absolute;right:98px;top:182px;display:flex;gap:10px}
.social span{width:38px;height:38px;border-radius:50%;border:2px solid #ddd;display:flex;align-items:center;justify-content:center}
</style>
</head>
<body>

<header class="hero">
  <div class="hero-photo" role="img" aria-label="Silver sports car on an open road at sunset"></div>
  <div class="brand"><span class="brand-dot"></span>Mesa Glass Tint</div>
  <div class="call">
    <span class="call-icon"><svg width="14" height="14" viewBox="0 0 24 24"><path fill="#6ed30d" d="M6.6 10.8a15 15 0 0 0 6.6 6.6l2.2-2.2a1 1 0 0 1 1-.25 11 11 0 0 0 3.6.6 1 1 0 0 1 1 1V20a1 1 0 0 1-1 1A17 17 0 0 1 3 4a1 1 0 0 1 1-1h3.5a1 1 0 0 1 1 1 11 11 0 0 0 .6 3.6 1 1 0 0 1-.25 1z"/></svg></span>
    GIVE US A CALL <b>555.014.2790</b>
  </div>
  <nav class="nav">
    <span class="active">HOME</span><span>WINDOW FILM SERVICES</span><span>FILM</span><span>ABOUT</span><span>GALLERY</span><span>CONTACT</span>
    <svg width="16" height="16" viewBox="0 0 24 24"><circle cx="10" cy="10" r="7" fill="none" stroke="#fff" stroke-width="3"/><path d="M15 15l6 6" stroke="#fff" stroke-width="3"/></svg>
  </nav>
  <h1 class="hero-title">MESA GLASS TINT</h1>
  <p class="hero-lead">We specialize in one thing and one thing only; Window Tinting.</p>
  <div class="btn-outline">GET MORE INFO</div>
  <div class="dots"><span class="on"></span><span></span><span></span><span></span></div>
  <svg class="abs" style="left:0;top:0" width="1200" height="541">
    <polygon points="960,541 1200,345 1200,541" fill="#fff"/>
    <polygon points="1010,541 1200,390 1200,541" fill="#6ed30d"/>
    <polygon points="1090,541 1200,455 1200,541" fill="#fff"/>
  </svg>
</header>

<h2 class="section-title" style="top:622px">WELCOME TO MESA GLASS TINT</h2>
<p class="intro">Mesa Tinting is not just another tint shop. We specialize in one thing and one thing only; Window Tinting. We offer Residential, Commercial and Automotive tinting services. Our philosophy is simple; do things right the first time!</p>

<svg class="abs" style="left:570px;top:758px" width="60" height="30">
  <path d="M20 4L8 15l12 11" fill="none" stroke="#bbb" stroke-width="5"/>
  <path d="M40 4l12 11-12 11" fill="none" stroke="#bbb" stroke-width="5"/>
</svg>

<article class="card" style="left:98px;top:750px;width:302px;height:490px">
  <svg class="frame" width="302" height="490"><polygon points="1,1 301,54 301,489 1,489" fill="#fff" stroke="#cfcfcf" stroke-width="1.5"/></svg>
  <svg class="icon" style="top:100px" width="100" height="100" viewBox="0 0 100 100">
    <circle cx="28" cy="26" r="16" fill="#6ed30d"/><circle cx="60" cy="26" r="16" fill="#6ed30d"/>
    <rect x="10" y="46" width="64" height="46" rx="4" fill="#6ed30d"/>
    <polygon points="74,60 96,48 96,90 74,78" fill="#6ed30d"/>
  </svg>
  <h3 style="top:246px">Automotive Film</h3>
  <p style="top:288px">Mesa Tint owner Dale Harmon and his staff of professional installers work with two of the world's finest window film manufacturers, Lumacore and Solvane</p>
  <div class="btn-small" style="top:398px">READ MORE</div>
</article>

<article class="card" style="left:450px;top:800px;width:302px;height:440px">
  <svg class="frame" width="302" height="440"><polygon points="1,1 151,30 301,1 301,439 1,439" fill="#fff" stroke="#cfcfcf" stroke-width="1.5"/></svg>
  <svg class="icon" style="top:72px" width="100" height="110" viewBox="0 0 100 110">
    <rect x="6" y="4" width="58" height="104" fill="#6ed30d"/>
    <rect x="64" y="48" width="32" height="60" fill="#6ed30d"/>
    <g fill="#fff"><rect x="16" y="16" width="10" height="12"/><rect x="32" y="16" width="10" height="12"/><rect x="48" y="16" width="10" height="12"/><rect x="16" y="38" width="10" height="12"/><rect x="32" y="38" width="10" height="12"/><rect x="48" y="38" width="10" height="12"/><rect x="16" y="60" width="10" height="12"/><rect x="48" y="60" width="10" height="12"/><rect x="28" y="84" width="16" height="24"/><rect x="74" y="60" width="12" height="12"/><rect x="74" y="82" width="12" height="12"/></g>
  </svg>
  <h3 style="top:222px">Commercial &amp; Residential</h3>
  <p style="top:266px">Window film is a sheet of coating that, with proper installation by Mesa Tint, can deliver energy savings similar to that offered by premium replacement</p>
  <div class="btn-small" style="top:378px">READ MORE</div>
</article>

<article class="card" style="left:800px;top:750px;width:302px;height:490px">
  <svg class="frame" width="302" height="490"><polygon points="1,54 301,1 301,489 1,489" fill="#fff" stroke="#cfcfcf" stroke-width="1.5"/></svg>
  <svg class="icon" style="top:92px" width="100" height="120" viewBox="0 0 100 120">
    <path d="M50 6L90 22v36c0 28-18 46-40 56C28 104 10 86 10 58V22z" fill="#6ed30d"/>
  </svg>
  <h3 style="top:246px">Clear Bra</h3>
  <p style="top:288px">Clear bra, or Paint Protection Film (PPF), is a clear urethane that certified Mesa Tint installers attach to the finish of those areas of your vehicle prone to minor</p>
  <div class="btn-small" style="top:398px">READ MORE</div>
</article>

<section class="services">
  <div class="services-photo" role="img" aria-label="Blurred car driving on a highway at dusk"></div>
  <svg class="abs" style="left:0;top:0" width="1200" height="523">
    <polygon points="0,0 110,0 0,90" fill="#6ed30d"/>
    <polygon points="0,523 110,523 0,433" fill="#6ed30d"/>
    <polygon points="1200,0 1090,0 1200,90" fill="#6ed30d"/>
    <polygon points="1200,523 1090,523 1200,433" fill="#6ed30d"/>
    <polygon points="1030,0 1070,0 1200,108 1200,140" fill="#fff"/>
    <polygon points="1030,523 1070,523 1200,415 1200,383" fill="#fff"/>
  </svg>
  <h2>WINDOW FILM SERVICES</h2>
  <p class="lead">With over 20 years experience in the valley auto tint market, you can be assured your car will be tinted professionally..</p>
  <div class="svc" style="top:195px">
    <div class="svc-ring"><svg width="34" height="26" viewBox="0 0 34 26"><path d="M6 10l4-8h14l4 8h3v10h-3v4h-5v-4H11v4H6v-4H3V10z" fill="#6ed30d"/></svg></div>
    <div><h4>AUTOMOTIVE</h4><span>All makes. All models.</span></div>
  </div>
  <div class="svc" style="top:288px">
    <div class="svc-ring"><svg width="24" height="32" viewBox="0 0 24 32"><rect x="2" y="0" width="20" height="32" fill="#6ed30d"/><g fill="#222"><rect x="6" y="4" width="4" height="4"/><rect x="14" y="4" width="4" height="4"/><rect x="6" y="12" width="4" height="4"/><rect x="14" y="12" width="4" height="4"/><rect x="9" y="24" width="6" height="8"/></g></svg></div>
    <div><h4>COMMERCIAL</h4><span>Store-fronts, Offices &amp; More.</span></div>
  </div>
  <div class="svc" style="top:381px">
    <div class="svc-ring"><svg width="32" height="28" viewBox="0 0 32 28"><path d="M16 0L0 14h4v14h9v-9h6v9h9V14h4z" fill="#6ed30d"/></svg></div>
    <div><h4>RESIDENTIAL</h4><span>Make Your Home Efficient.</span></div>
  </div>
  <div class="services-photo-frame" role="img" aria-label="Woman leaning on a car door against the setting sun"></div>
</section>

<h2 class="section-title" style="top:1940px">LATEST BLOG</h2>

<article class="post" style="left:98px">
  <div class="post-photo" role="img" aria-label="Couple smiling inside a car" style="background:radial-gradient(ellipse 120px 90px at 220px 90px,rgba(230,200,170,.8),rgba(0,0,0,0) 70%),radial-gradient(ellipse 140px 100px at 70px 120px,rgba(60,70,85,.7),rgba(0,0,0,0) 70%),linear-gradient(135deg,#9aa8b3,#c9b8a4 50%,#4b5560)"></div>
  <h3>Things to Consider When Choosing..</h3>
  <div class="meta"><svg width="12" height="12"><rect x="1" y="2" width="10" height="9" fill="#6ed30d"/></svg>June 27, 2017 &nbsp;| <svg width="12" height="12"><circle cx="6" cy="4" r="3" fill="#6ed30d"/><rect x="1" y="8" width="10" height="4" rx="2" fill="#6ed30d"/></svg>mesatint</div>
  <p>Are considering investing in window tints for your home, office, or vehicle?</p>
  <div class="more">READ MORE</div>
</article>
<article class="post" style="left:438px">
  <div class="post-photo" role="img" aria-label="Hands on a steering wheel in traffic" style="background:radial-gradient(ellipse 200px 60px at 162px 160px,rgba(25,25,30,.9),rgba(0,0,0,0) 75%),radial-gradient(ellipse 60px 20px at 250px 75px,rgba(190,60,60,.7),rgba(0,0,0,0) 70%),linear-gradient(180deg,#c3d1dc,#8a949c 45%,#2e3136)"></div>
  <h3>How dark is too dark for auto..</h3>
  <div class="meta"><svg width="12" height="12"><rect x="1" y="2" width="10" height="9" fill="#6ed30d"/></svg>May 22, 2017 &nbsp;| <svg width="12" height="12"><circle cx="6" cy="4" r="3" fill="#6ed30d"/><rect x="1" y="8" width="10" height="4" rx="2" fill="#6ed30d"/></svg>mesatint</div>
  <p>A classic accessory that has been added to cars for dozens of years. It is a cool add-on..</p>
  <div class="more">READ MORE</div>
</article>
<article class="post" style="left:778px">
  <div class="post-photo" role="img" aria-label="Silver car on a country road under a bright sky" style="background:radial-gradient(ellipse 90px 40px at 220px 110px,rgba(200,205,212,.95),rgba(0,0,0,0) 70%),radial-gradient(ellipse 120px 40px at 80px 115px,rgba(255,245,210,.9),rgba(0,0,0,0) 70%),linear-gradient(180deg,#5f93d4,#cfe0f0 58%,#8b7a5e 70%,#4e4a44)"></div>
  <h3>5 Commercial Window Tint Tips..</h3>
  <div class="meta"><svg width="12" height="12"><rect x="1" y="2" width="10" height="9" fill="#6ed30d"/></svg>April 27, 2017 &nbsp;| <svg width="12" height="12"><circle cx="6" cy="4" r="3" fill="#6ed30d"/><rect x="1" y="8" width="10" height="4" rx="2" fill="#6ed30d"/></svg>mesatint</div>
  <p>When you are ready to have your commercial window tint applied, you know that.</p>
  <div class="more">READ MORE</div>
</article>

<section class="gallery">
  <div class="gallery-photo" role="img" aria-label="Car side mirror reflecting an evening sky"></div>
  <svg class="abs" style="left:0;top:0" width="1200" height="100">
    <polygon points="0,0 1200,0 1200,5 600,90 0,5" fill="#fff"/>
    <polyline points="0,5 600,90 1200,5" fill="none" stroke="#6ed30d" stroke-width="6"/>
  </svg>
  <h2>GALLERY</h2>
  <div class="tile" role="img" aria-label="Chrome car door handle" style="left:100px;top:223px;background:radial-gradient(ellipse 90px 30px at 120px 100px,#f4f4f4,rgba(255,255,255,0) 70%),linear-gradient(135deg,#d8d8d8,#8c8c8c)"></div>
  <div class="tile" role="img" aria-label="Hand opening a white car door" style="left:357px;top:223px;background:radial-gradient(ellipse 60px 80px at 70px 90px,rgba(120,90,70,.6),rgba(0,0,0,0) 70%),linear-gradient(135deg,#f1f1f1,#6b6f73)"></div>
  <div class="tile" role="img" aria-label="Blue sports car rear lights" style="left:613px;top:223px;background:radial-gradient(ellipse 90px 50px at 120px 130px,rgba(235,240,245,.8),rgba(0,0,0,0) 70%),linear-gradient(135deg,#2d6fb0,#1e4e86 60%,#c9d4df)"></div>
  <div class="tile" role="img" aria-label="Headlight with raindrops" style="left:867px;top:223px;background:radial-gradient(ellipse 80px 60px at 140px 120px,rgba(230,235,240,.7),rgba(0,0,0,0) 70%),linear-gradient(135deg,#5a6570,#cfd6dc)"></div>
  <div class="tile" role="img" aria-label="Side mirror on an open road" style="left:100px;top:451px;background:radial-gradient(ellipse 90px 50px at 110px 80px,rgba(170,195,215,.8),rgba(0,0,0,0) 70%),linear-gradient(160deg,#8ca3b8,#3d4247)"></div>
  <div class="tile" role="img" aria-label="Modern car headlight close-up" style="left:357px;top:451px;background:radial-gradient(ellipse 80px 50px at 120px 90px,rgba(220,230,240,.7),rgba(0,0,0,0) 70%),linear-gradient(135deg,#1f2a36,#7f95a8)"></div>
  <div class="tile" role="img" aria-label="White car side mirror" style="left:613px;top:451px;background:radial-gradient(ellipse 70px 50px at 110px 110px,rgba(40,40,45,.5),rgba(0,0,0,0) 70%),linear-gradient(135deg,#ffffff,#9aa0a5)"></div>
  <div class="tile" role="img" aria-label="Car mirror at sunset" style="left:867px;top:451px;background:radial-gradient(ellipse 100px 30px at 100px 120px,rgba(255,190,110,.9),rgba(0,0,0,0) 70%),linear-gradient(180deg,#3b4d66,#e08a4a 60%,#2b2624)"></div>
  <div class="btn-green">VIEW MORE</div>
</section>

<footer class="footer">
  <div class="contact" style="left:255px">
    <span class="ring"><svg width="14" height="18" viewBox="0 0 14 18"><path d="M7 0a7 7 0 0 1 7 7c0 5-7 11-7 11S0 12 0 7a7 7 0 0 1 7-7z" fill="#fff"/><circle cx="7" cy="7" r="2.5" fill="#1b1b1b"/></svg></span>
    <span>4120 N. Sandstone Rd. Suite B<br>Dry Wash, Az. 85000</span>
  </div>
  <div class="contact" style="left:548px;top:51px">
    <span class="ring"><svg width="16" height="16" viewBox="0 0 24 24"><path fill="#fff" d="M6.6 10.8a15 15 0 0 0 6.6 6.6l2.2-2.2a1 1 0 0 1 1-.25 11 11 0 0 0 3.6.6 1 1 0 0 1 1 1V20a1 1 0 0 1-1 1A17 17 0 0 1 3 4a1 1 0 0 1 1-1h3.5a1 1 0 0 1 1 1 11 11 0 0 0 .6 3.6 1 1 0 0 1-.25 1z"/></svg></span>
    <span>555.014.2790</span>
  </div>
  <div class="contact" style="left:753px;top:51px">
    <span class="ring"><svg width="18" height="14" viewBox="0 0 18 14"><rect width="18" height="14" fill="#fff"/><path d="M0 0l9 7 9-7" fill="none" stroke="#1b1b1b" stroke-width="1.5"/></svg></span>
    <span>dale@mesaglass.example</span>
  </div>
  <div class="foot-links">Home &nbsp;&nbsp;| &nbsp;&nbsp;Window Film Services &nbsp;&nbsp;| &nbsp;&nbsp;Film &nbsp;&nbsp;| &nbsp;&nbsp;About &nbsp;&nbsp;| &nbsp;&nbsp;Gallery &nbsp;&nbsp;| &nbsp;&nbsp;Contact</div>
  <div class="foot-rule"></div>
  <div class="copy">Copyrights © 2017, Mesa Glass Tint. All rights reserved.</div>
  <div class="social" aria-label="Social links">
    <span><svg width="16" height="16" viewBox="0 0 16 16"><circle cx="12" cy="3" r="2.3" fill="#fff"/><circle cx="4" cy="8" r="2.3" fill="#fff"/><circle cx="12" cy="13" r="2.3" fill="#fff"/><path d="M12 3L4 8l8 5" fill="none" stroke="#fff" stroke-width="1.4"/></svg></span>
    <span><svg width="16" height="16" viewBox="0 0 16 16"><circle cx="8" cy="8" r="6.5" fill="none" stroke="#fff" stroke-width="1.4"/><ellipse cx="8" cy="8" rx="3" ry="6.5" fill="none" stroke="#fff" stroke-width="1.2"/><path d="M1.5 8h13" stroke="#fff" stroke-width="1.2"/></svg></span>
    <span><svg width="16" height="16" viewBox="0 0 16 16"><path d="M2 3h12v8H7l-3 3v-3H2z" fill="#fff"/></svg></span>
  </div>
</footer>

</body>
</html>
```